Design a single page Shopify store web page

We are looking to have a page designed for a single page Shopify store with 2 products. We already have a basic structure that we like, though we are open to suggestions. We are looking for somebody to provide a design/color scheme that we can then implement using Shopify's templating system. We can handle the implementation(HTML / CSS / jS) as we already have 2 web developers on the team, but have not been able to find a design we liked.

The job would consist of providing a mockup (photoshop or otherwise) and any vector graphics you choose to create for the site (we can provide product photos and other images).

You can also look at http://brickdune.com.au for some of our design direction we have used so far

Target Market(s)

Young Australian Males (18 - 49)

Industry/Entity Type

Store

Number of Pages Required

1 page

Font styles to use
Serif
Sans Serif

Requirements
Must have
• Single Page Design
• E-commerce Product Purchase
• Manly (whatever interpretation of that you have)

```html
<!DOCTYPE html>
<html lang="en">
<head>
<meta charset="utf-8">
<title>Brick Dune — Underwear &amp; Socks Delivered</title>
<link rel="stylesheet" href="https://fonts.googleapis.com/css2?family=Yanone+Kaffeesatz:wght@500&family=Roboto:wght@400;700&display=swap">
<style>
  :root {
    --ink-dark: #0a1011;
    --hero-deep: #0f0d0c;
    --hero-mid: #4a433b;
    --hero-light: #8c8273;
    --text-light: #f4f4f2;
    --accent-green: #9dcb6b;
  }
  * { box-sizing: border-box; margin: 0; padding: 0; }
  html, body { width: 1200px; height: 710px; overflow: hidden; background: var(--ink-dark); }
  .page { position: relative; width: 1200px; height: 710px; overflow: hidden; }

  .hero { position: absolute; left: 0; top: 0; width: 1200px; height: 592px; }
  .hero-photo {
    position: absolute; inset: 0;
    background:
      radial-gradient(ellipse 300px 420px at 480px 250px, var(--hero-light) 0%, var(--hero-mid) 45%, transparent 80%),
      linear-gradient(90deg, var(--hero-deep) 0%, #24201c 40%, #1c1916 70%, var(--hero-deep) 100%);
  }
  .hero-brand {
    position: absolute; left: 97px; top: 68px;
    font-family: "Yanone Kaffeesatz", sans-serif; font-weight: 500;
    font-size: 108px; line-height: 92px; color: var(--text-light);
  }
  .hero-brand span { display: block; }
  .hero-brand .second { padding-left: 60px; }

  .social { position: absolute; top: 19px; right: 112px; display: flex; gap: 12px; }
  .social-link {
    display: block; height: 46px; padding: 0 10px; border-radius: 4px;
    background: var(--text-light); color: var(--ink-dark);
    font-family: "Roboto", sans-serif; font-weight: 700; font-size: 13px;
    line-height: 46px; text-decoration: none;
  }

  .tagline {
    position: absolute; right: 99px; top: 246px; text-align: right;
    font-family: "Yanone Kaffeesatz", sans-serif; font-weight: 500;
    color: var(--text-light); font-size: 52px; line-height: 54px;
  }
  .tagline p + p { margin-top: 4px; }

  .slider-dots { position: absolute; top: 553px; left: 540px; display: flex; gap: 18px; }
  .dot { width: 17px; height: 17px; border-radius: 50%; border: 3px solid var(--text-light); }
  .dot.active { background: var(--text-light); }

  .site-nav {
    position: absolute; left: 0; top: 592px; width: 1200px; height: 118px;
    background: var(--ink-dark);
  }
  .nav-brand {
    position: absolute; left: 81px; top: 10px;
    font-family: "Yanone Kaffeesatz", sans-serif; font-weight: 500;
    font-size: 50px; line-height: 48px; color: var(--text-light);
  }
  .nav-brand span { display: block; }
  .nav-brand .second { padding-left: 32px; }
  .nav-links { position: absolute; left: 357px; top: 45px; display: flex; list-style: none; }
  .nav-links a {
    font-family: "Roboto", sans-serif; font-size: 20px; color: var(--text-light);
    text-decoration: none; display: block; padding-bottom: 6px;
  }
  .nav-links li { margin-right: 67px; }
  .nav-links a.current { border-bottom: 2px solid var(--text-light); }
  .cta {
    position: absolute; left: 964px; top: 30px; width: 154px; height: 60px;
    border-radius: 6px; background: var(--accent-green); color: var(--text-light);
    font-family: "Roboto", sans-serif; font-weight: 700; font-size: 20px;
    line-height: 60px; text-align: center; text-decoration: none;
  }
</style>
</head>
<body>
<div class="page">
  <section class="hero">
    <div class="hero-photo" role="img" aria-label="Black and white studio photo of a muscular man's torso wearing black briefs"></div>
    <h1 class="hero-brand"><span>Brick</span><span class="second">Dune</span></h1>
    <nav class="social">
      <a class="social-link" href="#">Facepage</a>
      <a class="social-link" href="#">Chirper</a>
    </nav>
    <div class="tagline">
      <p>Automate your Life<br>New Underwear and<br>Socks</p>
      <p>Delivered to your door<br>when you NEED it</p>
    </div>
    <div class="slider-dots">
      <span class="dot active"></span><span class="dot"></span><span class="dot"></span><span class="dot"></span>
    </div>
  </section>
  <header class="site-nav">
    <div class="nav-brand"><span>Brick</span><span class="second">Dune</span></div>
    <ul class="nav-links">
      <li><a class="current" href="#">How it works</a></li>
      <li><a href="#">Plans</a></li>
      <li><a href="#">FAQ</a></li>
      <li><a href="#">About us</a></li>
    </ul>
    <a class="cta" href="#">Sign up now!</a>
  </header>
</div>
</body>
</html>
```